2018 Vision Board Workshop

I need to promote this workshop on both an 8.5x11 sheet and a 5x7 card. I do have a logo that needs to be present. I'd like to stay true to my branded colors. The flyer needs to project the excitement of a new year and the possibilities of what a person can create, produce, explore in their lives by putting it all on a vision board. Creating the vision of what you want will inspire you to achieve your goals and dreams. Looking at your vision board each day will propel you into taking action as you chart your course to achieve what you truly want.
The flyer needs to have the following information:
The workshop date and time - Sat., Jan. 13, 2018, 10:30-1:30
The location is - Studio 47B, 2486 Maple Ridge Ln, Colorado Springs, Co 80920
in the BUILD Room
My name and contact information - Mara Lindqvist
Text and voice 303-614-7752
Email - mara@bright-path-forward.com
Website - bright-path-forward.com
The fee is $45. All materials are provided.

My company is called Bright Path Forward. I am a Life Coach, author, speaker and workshop leader.\ I wrote this program, Bright Path Forward to teach concepts and supporting skills for living with more happiness, satisfaction and fulfillment. Thanks for reading this!! Mara

Target Market(s)

Primarily women, educated, motivated, proactive in their own lives and well being

Font styles to use
Other font styles liked:
• I have been using Century Gothic. I'm open to new ideas.

Requirements
Must have
• The Bright Path Forward logo
• The flyer needs to have the following information:
• The workshop date and time - Sat., Jan. 13, 2018, 10:30-1:30
• The location is - Studio 47B, 2486 Maple Ridge Ln, Colorado Springs, Co 80920
• in the BUILD Room
• My name and contact information - Mara Lindqvist
• Text and voice 303-614-7752
• Email - mara@bright-path-forward.com
• Website - bright-path-forward.com
• The fee is $45. All materials are provided.
Nice to have
• The Bright Path Forward branded colors in the design
• Images of vision boards

```html
<!DOCTYPE html>
<html lang="en">
<head>
<meta charset="utf-8">
<title>2018 Vision Board Workshop</title>
<link href="https://fonts.googleapis.com/css2?family=Source+Sans+3:ital,wght@0,400;0,600;0,700;1,400&display=swap" rel="stylesheet">
<style>
  :root {
    --brand-blue: #1f73c0;
    --bright-blue: #2aa3f0;
    --lime: #84d41c;
    --ink: #454545;
    --paper: #f3f4f5;
    --ribbon: #5d5e60;
    --backdrop: #e7e5e2;
  }
  * { margin: 0; padding: 0; box-sizing: border-box; }
  html, body { width: 1200px; height: 1200px; overflow: hidden; background: var(--backdrop); }
  body { font-family: "Source Sans 3", "Segoe UI", sans-serif; }
  .flyer {
    position: absolute; left: 150px; top: 18px; width: 900px; height: 1164px;
    background: var(--paper); overflow: hidden;
    box-shadow: 0 6px 24px rgba(0,0,0,.18);
  }
  .flyer-shapes { position: absolute; inset: 0; }
  .brand {
    position: absolute; left: 118px; top: 96px;
    display: flex; align-items: center; gap: 10px;
    font-size: 32px; font-weight: 400; color: var(--lime);
  }
  .brand-dot { width: 16px; height: 16px; border-radius: 50%; background: var(--bright-blue); }
  .headline { position: absolute; left: 0; right: 0; text-align: center; font-weight: 700; }
  .headline-year { top: 485px; font-size: 70px; color: var(--brand-blue); line-height: 80px; }
  .headline-title { top: 566px; font-size: 68px; color: var(--ink); letter-spacing: -0.5px; line-height: 80px; }
  .rule { position: absolute; height: 1px; background: #d2d4d6; }
  .rule-title { left: 150px; right: 150px; top: 656px; }
  .event-date { top: 672px; font-size: 38px; color: var(--brand-blue); font-weight: 600; line-height: 48px; }
  .event-time { top: 725px; font-size: 37px; color: var(--ink); font-weight: 600; line-height: 48px; }
  .location-label {
    position: absolute; left: 0; right: 0; top: 790px; text-align: center;
    font-size: 23px; font-weight: 700; color: var(--brand-blue); line-height: 30px;
  }
  .rule-loc-left { left: 245px; width: 150px; top: 806px; background: #b9bcc0; }
  .rule-loc-right { left: 515px; width: 210px; top: 806px; background: #b9bcc0; }
  .location-address {
    position: absolute; left: 0; right: 0; top: 822px; text-align: center;
    font-size: 23.5px; font-weight: 600; color: var(--ink); line-height: 28px;
  }
  .host-portrait {
    position: absolute; left: 56px; top: 923px; width: 184px; height: 184px; border-radius: 50%;
    border: 7px solid var(--lime); box-shadow: inset 0 0 0 4px var(--bright-blue);
    background: radial-gradient(circle at 50% 45%, #e8c9a8 0%, #c9a070 45%, #8c7a3e 100%);
  }
  .host-name {
    position: absolute; left: 257px; top: 976px; height: 24px; width: 150px;
    background: var(--lime); color: #fff; font-size: 18px; font-weight: 700;
    line-height: 24px; padding-left: 8px;
    clip-path: polygon(0 0, 100% 0, 93% 100%, 0 100%);
  }
  .host-contact {
    position: absolute; left: 262px; display: flex; align-items: center; gap: 8px;
    font-size: 18px; color: var(--ink);
  }
  .host-phone { top: 1008px; }
  .host-email { top: 1033px; }
  .host-contact svg { width: 13px; height: 13px; }
  .fee-badge {
    position: absolute; left: 613px; top: 880px; width: 202px; height: 202px; border-radius: 50%;
    background: #fff; border: 6px solid var(--lime); box-shadow: inset 0 0 0 5px var(--bright-blue), 0 8px 14px rgba(0,0,0,.15);
  }
  .fee-label {
    position: absolute; left: 614px; top: 900px; width: 96px; height: 32px;
    background: var(--ribbon); color: #fff; font-style: italic; font-size: 25px;
    line-height: 32px; padding-left: 12px;
    clip-path: polygon(4% 0, 100% 0, 92% 100%, 0 100%);
  }
  .fee-amount {
    position: absolute; left: 613px; width: 202px; top: 940px; text-align: center;
    font-size: 62px; font-weight: 700; color: #333;
  }
  .fee-note {
    position: absolute; left: 605px; top: 1021px; width: 218px; height: 38px;
    background: var(--ribbon); color: #fff; font-style: italic; font-size: 18px;
    line-height: 38px; text-align: center;
    clip-path: polygon(2% 0, 100% 0, 98% 100%, 0 100%);
  }
  .site-url {
    position: absolute; left: 257px; top: 1105px; font-size: 15px; letter-spacing: 1.6px; color: #fff;
  }
</style>
</head>
<body>
  <main class="flyer">
    <svg class="flyer-shapes" viewBox="0 0 900 1164" width="900" height="1164">
      <defs>
        <linearGradient id="photoTone" x1="0" y1="0" x2="0.35" y2="1">
          <stop offset="0" stop-color="#f7f7f6"/>
          <stop offset="0.3" stop-color="#eee4da"/>
          <stop offset="0.6" stop-color="#d9b79b"/>
          <stop offset="0.8" stop-color="#9db7d6"/>
          <stop offset="1" stop-color="#5c5f66"/>
        </linearGradient>
        <radialGradient id="windowGlow" cx="0.3" cy="0.25" r="0.45">
          <stop offset="0" stop-color="#ffffff" stop-opacity="0.95"/>
          <stop offset="1" stop-color="#ffffff" stop-opacity="0"/>
        </radialGradient>
      </defs>
      <g role="img" aria-label="Photo of a smiling family of four lying together">
        <rect x="0" y="0" width="900" height="470" fill="url(#photoTone)"/>
        <rect x="0" y="0" width="900" height="470" fill="url(#windowGlow)"/>
      </g>
      <path d="M0,0 H150 C86,112 82,238 150,312 C172,338 188,372 200,420 L0,440 Z" fill="#fff"/>
      <path d="M0,0 H132 C72,110 68,240 140,315 C160,340 175,375 188,420 L0,440 Z" fill="var(--brand-blue)"/>
      <path d="M142,0 C78,111 75,239 145,313 C166,339 181,373 194,420" fill="none" stroke="var(--lime)" stroke-width="5"/>
      <path d="M0,430 C200,390 350,420 520,448 C700,478 830,425 900,345 V1164 H0 Z" fill="var(--lime)"/>
      <path d="M0,444 C200,404 350,434 520,462 C700,492 830,440 900,362 V1164 H0 Z" fill="var(--paper)"/>
      <path d="M900,690 C885,820 868,960 846,1164 H900 Z" fill="var(--lime)"/>
      <path d="M900,712 C890,830 876,970 860,1164 H900 Z" fill="var(--brand-blue)"/>
      <path d="M0,1088 C250,1076 560,1084 900,1134 V1164 H0 Z" fill="var(--lime)"/>
      <path d="M0,1100 C250,1090 560,1098 900,1150 V1164 H0 Z" fill="var(--brand-blue)"/>
    </svg>

    <div class="brand"><span class="brand-dot"></span>Bright Path Forward</div>

    <h1 class="headline headline-year">2018</h1>
    <h2 class="headline headline-title">Vision Board Workshop</h2>
    <div class="rule rule-title"></div>

    <p class="headline event-date">Date: Saturday, January 13, 2018</p>
    <p class="headline event-time">Time: 10:30-1:30</p>

    <div class="rule rule-loc-left"></div>
    <p class="location-label">LOCATION</p>
    <div class="rule rule-loc-right"></div>
    <p class="location-address">Studio 47B, 2486 Maple Ridge Ln, Colorado Springs, Co 80920<br>in the BUILD Room</p>

    <div class="host-portrait" role="img" aria-label="Portrait of workshop leader Mara Lindqvist"></div>
    <p class="host-name">Mara Lindqvist</p>
    <p class="host-contact host-phone">
      <svg viewBox="0 0 16 16"><path d="M4 1 L6 5 L4.5 6.5 C5.5 8.5 7.5 10.5 9.5 11.5 L11 10 L15 12 L14 15 C7 15 1 9 1 2 Z" fill="var(--bright-blue)"/></svg>
      303-614-7752
    </p>
    <p class="host-contact host-email">
      <svg viewBox="0 0 16 16"><rect x="1" y="3" width="14" height="10" rx="1" fill="var(--bright-blue)"/><path d="M1.5 4 L8 9 L14.5 4" fill="none" stroke="#fff" stroke-width="1.4"/></svg>
      mara@bright-path-forward.com
    </p>

    <div class="fee-badge"></div>
    <p class="fee-label">Fee is</p>
    <p class="fee-amount">$45</p>
    <p class="fee-note">All materials are provided</p>

    <p class="site-url">www.bright-path-forward.com</p>
  </main>
</body>
</html>
```